Meadow Paw Web Site

We have basically a start up business that I need help with. This project is just for the web site.

Our product is a frozen raw pet food that promotes weight control, less shedding, smaller stools and an overall better health. The product is in nugget form similar to what you would see in a steak shish kabob. I only share that with you in case you want to incorporate that in the design.

We have been in business for 17 years but all of our sales have been word of mouth. We are going to be launching an infomercial this summer and I need everything stated previously to be completed before we can launch the infomercial.

We need the following (6) pages:

Home:
This is where we need to have the ability to purchase our products. Our main goal is to get the consumer to purchase our product. We have our own shopping cart so we just need to allow for the insertion of that shopping cart.

Why Raw:
This will just be a page with 4-5 paragraphs and an embedded YouTube video.

How to Use:
We will need a page with a chart (4 Columns wide with 6 rows) as well as an embedded YouTube video.

Customer Success Stories:
Allow us to add these as we move forward. I need a placeholder for an image of the customers pet and a paragraph or two explaining the situation

Where to Buy:
- Online - Find a Retailer - Find a Local Distributor - Call to Order

Contact Us:
Copper Ridge Holdings, Inc.
2740 Copper Rd
Eagan, MN 55148
(800) xxx-xxxx

We need to provide links to our to be created... Facebook page, Twitter Account, Youtube Channel, Google circle, Blog
Updates

All, I have received many front page designs that look good.  Please notice in the brief that I need multiple pages built not just the home page.  

Thanks,

Dale

Reason: I need to see the rest of the pages. Thanks, Dale

Target Market(s)

Women between the ages of 30 & 60.

Industry/Entity Type

Shopping

```html
<!DOCTYPE html>
<html lang="en">
<head>
<meta charset="utf-8">
<title>Meadow Paw – Contact Us</title>
<link href="https://fonts.googleapis.com/css2?family=Oswald:wght@300;400&family=PT+Sans:wght@400;700&family=Dosis:wght@400;500&display=swap" rel="stylesheet">
<style>
:root{
  --orange:#c04a00;
  --orange-deep:#c03f00;
  --nav-top:#ec8a18;
  --nav-bottom:#cc5e04;
  --yellow:#f7d21a;
  --ink:#2b2b2b;
  --olive:#3a3000;
  --field-border:#ecc9cf;
  --card-border:#e6dada;
  --footer:#2d2d2f;
  --footer-base:#1b1b1c;
  --footer-text:#a9a9a9;
  --footer-head:#ececec;
}
*{box-sizing:border-box;margin:0;padding:0}
html,body{width:1200px;height:1104px;overflow:hidden}
body{position:relative;font-family:"PT Sans",sans-serif;color:var(--ink);
  background:linear-gradient(#f6ecec 196px,#fbf6f6 500px,#fff 785px)}
.abs{position:absolute}
.header-band{left:0;top:0;width:1200px;height:196px;background:linear-gradient(90deg,#e6e2dd,#ebe8e4 50%,#d8d5d1)}
.brand-mark{left:120px;top:36px;width:200px;height:116px;border-radius:6px;
  background:linear-gradient(#f8b014,#e46e06);display:flex;align-items:center;justify-content:center}
.brand-mark span{font:700 28px "PT Sans",sans-serif;color:#1a1a1a}
.account-links{right:123px;top:25px;font:700 11px "PT Sans",sans-serif;color:var(--orange);letter-spacing:.2px;text-transform:uppercase}
.account-links i{font-style:normal;margin:0 6px}
.pill{top:64px;height:26px;border-radius:13px;font-size:13px;display:flex;align-items:center;justify-content:center}
.pill.signin{left:905px;width:83px;background:linear-gradient(#e5751a,#c04a00);color:#fff}
.pill.register{left:997px;width:83px;background:linear-gradient(#ffe454,#f2c400);color:#3a2a00}
.cart{left:623px;top:118px}
.cart-label{left:663px;top:124px;font:400 15px "Oswald",sans-serif;color:var(--orange)}
.cart-count{left:787px;top:124px;font:400 15px "Oswald",sans-serif;color:var(--orange)}
.search{left:865px;top:117px;width:215px;height:32px;border-radius:16px;background:#fff;border:1px solid #e2d8d2;
  padding:0 18px;display:flex;align-items:center;justify-content:space-between;font-size:13px;color:var(--orange)}
.main-nav{left:120px;top:172px;width:960px;height:47px;border-radius:5px;border:1px solid #d86b05;
  background:linear-gradient(var(--nav-top),var(--nav-bottom));}
.main-nav a{position:absolute;top:0;height:45px;line-height:45px;font:400 19px/45px "Oswald",sans-serif;color:#fff;text-decoration:none;transform:translateX(-50%);white-space:nowrap}
.nav-divider{position:absolute;top:4px;width:2px;height:37px;background:linear-gradient(90deg,#b94f02,#f39a3a)}
.page-title{left:120px;top:262px;font:400 28px "Oswald",sans-serif;color:var(--olive)}
.page-title em{font-style:normal;color:var(--orange)}
.title-rule{left:120px;top:297px;width:957px;border-top:2px dotted #b9aaa4}
.card-stack{left:134px;top:722px;width:552px;height:10px;border:1px solid var(--card-border);border-top:0;border-radius:0 0 10px 10px;background:#fff}
.card-stack.two{left:127px;width:566px;top:718px;height:10px}
.contact-card{left:120px;top:336px;width:578px;height:388px;background:#fff;border:1px solid var(--card-border);border-radius:10px}
.card-heading{left:152px;top:358px;font:400 33px "Dosis",sans-serif;color:#333;letter-spacing:-.5px}
.card-rule{left:153px;top:424px;width:526px;border-top:1px solid #efd9db}
.field{border:1px solid var(--field-border);background:#fff;font:400 14px "PT Sans",sans-serif;color:#666;padding:0 20px;display:flex;align-items:center}
.field.name{left:151px;top:465px;width:197px;height:44px}
.field.email{left:151px;top:522px;width:197px;height:44px}
.field.subject{left:152px;top:579px;width:196px;height:44px}
.field.comment{left:358px;top:465px;width:322px;height:158px;align-items:flex-start;padding-top:14px;padding-left:25px}
.submit{left:581px;top:641px;width:98px;height:48px;border-radius:8px;background:var(--orange-deep);color:#fff;font:400 20px/48px "Oswald",sans-serif;text-align:center}
.side-brand{left:760px;top:338px;font:700 52px "PT Sans",sans-serif;color:#1a1a1a;letter-spacing:-1px}
.side-rule{left:760px;top:419px;width:320px;height:4px;background:#dcdcdc}
.side-intro{left:760px;top:451px;width:320px;font-size:14px;line-height:21px;color:#333;letter-spacing:-.3px}
.side-lines{font-size:14px;line-height:19px;color:#222}
.side-phones{left:761px;top:517px}
.side-mails{left:761px;top:573px}
.side-social{left:760px;top:635px;display:flex;gap:12px}
.side-social span{width:24px;height:24px;border-radius:3px;background:#555}
.side-social span.accent{background:var(--orange)}
.footer{left:0;top:785px;width:1200px;height:276px;background:var(--footer)}
.footer-base{left:0;top:1060px;width:1200px;height:44px;background:var(--footer-base)}
.footer-col{top:818px}
.footer-col h3{font:400 20px "Oswald",sans-serif;color:var(--footer-head);margin-bottom:12px}
.footer-col ul{list-style:none}
.footer-col li{font-size:13px;line-height:24px;color:var(--footer-text)}
.footer-sep{top:828px;height:190px;border-left:1px dotted #6b6b6b}
.info-lead{font-size:14px;color:var(--footer-text);line-height:20px}
.info-small{font-size:11px;color:var(--footer-text);line-height:20px;width:190px}
.info-phone{margin-top:6px;font:14px "PT Serif",serif;color:var(--footer-text);display:flex;align-items:center;gap:4px}
.news-text{font-size:13px;color:var(--footer-text);line-height:16px;width:215px}
.news-input{left:842px;top:902px;width:236px;height:32px;background:#fff;border:1px solid #ccc;font-size:15px;color:#bbb;padding:0 11px;display:flex;align-items:center}
.subscribe{left:993px;top:943px;width:86px;height:28px;background:var(--orange-deep);color:#fff;font-size:15px;display:flex;align-items:center;justify-content:center}
.footer-social{left:916px;top:986px;display:flex;gap:8px}
.footer-social span{width:26px;height:26px;border-radius:3px}
.copyright{left:121px;top:1076px;font-size:12px;color:#8a8a8a}
</style>
</head>
<body>
<div class="abs header-band"></div>

<div class="abs brand-mark" role="img" aria-label="Meadow Paw brand mark"><span>Meadow Paw</span></div>

<nav class="abs account-links">My Account<i>/</i>Wish List<i>/</i>My Cart<i>/</i>Checkout</nav>
<div class="abs pill signin">Sing in</div>
<div class="abs pill register">Register</div>

<svg class="abs cart" width="30" height="26" viewBox="0 0 30 26" aria-hidden="true">
  <path d="M9 10 L15 2 L21 10" fill="none" stroke="#d2680e" stroke-width="2"/>
  <path d="M1 10 H29 L25 24 H5 Z" fill="#e27614"/>
  <path d="M8 13 V21 M12 13 V21 M16 13 V21 M20 13 V21 M24 13 V21" stroke="#fff" stroke-width="1.5"/>
</svg>
<div class="abs cart-label">SHOPPING CART</div>
<div class="abs cart-count">(2) ITEMS</div>
<div class="abs search">Search.......
  <svg width="16" height="16" viewBox="0 0 16 16" aria-hidden="true"><circle cx="6.5" cy="6.5" r="5" fill="none" stroke="#c04a00" stroke-width="2.2"/><path d="M10 10 L15 15" stroke="#c04a00" stroke-width="2.6" stroke-linecap="round"/></svg>
</div>

<nav class="abs main-nav">
  <svg style="position:absolute;left:28px;top:14px" width="22" height="18" viewBox="0 0 22 18" aria-label="Home"><path d="M11 1 L21 9 H18 V17 H13 V12 H9 V17 H4 V9 H1 Z" fill="#fff"/></svg>
  <span class="nav-divider" style="left:77px"></span>
  <a style="left:146px">Why Raw</a>
  <span class="nav-divider" style="left:222px"></span>
  <a style="left:313px">How to Use</a>
  <span class="nav-divider" style="left:394px"></span>
  <a style="left:495px">Where to Buy</a>
  <span class="nav-divider" style="left:585px"></span>
  <a style="left:692px">Success Stories</a>
  <span class="nav-divider" style="left:800px"></span>
  <a style="left:885px">Contact Us</a>
</nav>

<h1 class="abs page-title">CONTACT <em>US</em></h1>
<div class="abs title-rule"></div>

<div class="abs card-stack"></div>
<div class="abs card-stack two"></div>
<div class="abs contact-card"></div>
<h2 class="abs card-heading">Reach Us</h2>
<div class="abs card-rule"></div>
<div class="abs field name">Name</div>
<div class="abs field email">Email</div>
<div class="abs field subject">Subject</div>
<div class="abs field comment">Your comment</div>
<div class="abs submit">Submit</div>

<div class="abs side-brand">meadow paw</div>
<div class="abs side-rule"></div>
<p class="abs side-intro">Lorem ipsum dolor sit amet, consectetur adipiscing elit. Sed viverra, urna quis dignissim .</p>
<div class="abs side-lines side-phones">+(00) 000 000 000<br>+(00) 000 000 000</div>
<div class="abs side-lines side-mails">hello@meadowpaw.com<br>sales@meadowpaw.com</div>
<div class="abs side-social" aria-label="Social links">
  <span></span><span></span><span></span><span class="accent"></span><span></span>
</div>

<footer class="abs footer"></footer>
<div class="abs footer-col" style="left:120px"><h3>Quick Links</h3>
  <ul><li>Why Raw</li><li>How to Use</li><li>Where to Buy</li><li>Success Stories</li><li>How to Use</li><li>Where to Buy</li><li>Contact Us</li></ul></div>
<div class="abs footer-sep" style="left:244px"></div>
<div class="abs footer-col" style="left:273px"><h3>Top Products</h3>
  <ul><li>Product 1</li><li>Product 2</li><li>Product 3</li><li>Product 4</li><li>Product 5</li><li>Product 6</li><li>Product 7</li></ul></div>
<div class="abs footer-sep" style="left:399px"></div>
<div class="abs footer-col" style="left:428px"><h3>Where to Buy</h3>
  <ul><li>Find a Retailer</li><li>Find a Local Distributor</li><li>Call to Order</li></ul></div>
<div class="abs footer-sep" style="left:582px"></div>
<div class="abs footer-col" style="left:616px"><h3>Contact Information</h3>
  <p class="info-lead">PUBLISHING PACKAGES</p>
  <p class="info-small">Lorem Ipsum is therefore always free from repetition</p>
  <p class="info-phone"><svg width="20" height="20" viewBox="0 0 20 20" aria-hidden="true"><path d="M4 2 L7 2 L8 6 L6 8 C7 11 9 13 12 14 L14 12 L18 13 L18 16 C18 17 17 18 16 18 C8 18 2 12 2 4 C2 3 3 2 4 2 Z" fill="#ddd"/></svg>+0 (000) 000-0000</p></div>
<div class="abs footer-sep" style="left:814px"></div>
<div class="abs footer-col" style="left:841px"><h3>Newsletter</h3>
  <p class="news-text">combined with a handful of model sentence structures.</p></div>
<div class="abs news-input">Email address</div>
<div class="abs subscribe">Subscribe</div>
<div class="abs footer-social" aria-label="Social links">
  <span style="background:#3b6fd0"></span><span style="background:#3c5066"></span><span style="background:#f49a12"></span><span style="background:#c93a2a"></span><span style="background:#b52a2a"></span>
</div>

<div class="abs footer-base"></div>
<p class="abs copyright">Company Name © 2014. Privacy Policy</p>
</body>
</html>
```